Website design with eCommerce for revolutionary new product in the manufacturing industry.

We need a website designed for a precision manufacturing company based in the suburbs of Minneapolis, Minnesota called Velkrin Manufacturing. We have a revolutionary new product, the TARN LOCK, to introduce and sell through an eCommerce storefront. The website would include company information, product information, and the storefront. Green is a color that represents Velkrin Manufacturing. The final design should communicate that we exclusively offer premium products at a premium price. The design should also let the customer know they are the focus of our work.

Target Market(s)

Machinists and machine shops

Industry/Entity Type

Manufacturing and machine shops

Coding

Coded - Design and coding required

Font styles to use
Sans Serif

Colors
59FF00
82FF00
B8FF75
E3FFCB
F4FFEA

Requirements
Must have
• eCommerce storefront, Made in USA references
Nice to have
• Home page, TARN LOCK Product page, About Us, Capabilities, Contact, etc.
Should not have
• Should not be too much text and reading.

```html
<!DOCTYPE html>
<html lang="en">
<head>
<meta charset="utf-8">
<title>Contact – Velkrin Manufacturing</title>
<link href="https://fonts.googleapis.com/css2?family=Poppins:ital,wght@0,400;0,500;0,600;0,700;0,800;1,700;1,800;1,900&display=swap" rel="stylesheet">
<style>
:root{
  --green:#59ff00;
  --ink:#111111;
  --white:#ffffff;
  --field:#f3f3f3;
  --muted:#cfcfcf;
  --photo-dark:#3a3c3a;
  --photo-mid:#5b5e5a;
  --social:#1f1f1f;
}
*{box-sizing:border-box;margin:0;padding:0}
html,body{width:1200px;height:2324px;overflow:hidden;background:var(--white)}
body{position:relative;font-family:"Poppins",sans-serif;color:var(--ink)}
.abs{position:absolute}

/* hero */
.hero-bg{left:0;top:0;width:1200px;height:430px}
.nav{left:90px;top:24px;width:1020px;height:67px;background:var(--white);border-radius:6px;box-shadow:0 4px 14px rgba(0,0,0,.12);display:flex;align-items:center;padding:0 16px}
.brand{font-weight:800;font-size:21px;letter-spacing:1px;color:var(--ink);margin-right:28px;white-space:nowrap}
.nav-links{display:flex;gap:15px;list-style:none;font-size:11px;font-weight:600;white-space:nowrap}
.nav-cta{margin-left:auto;background:var(--green);font-size:12px;font-weight:600;padding:9px 16px;border-radius:3px}
.hero-title{left:0;top:182px;width:1200px;text-align:center;color:var(--white);font-size:47px;font-style:italic;font-weight:800;letter-spacing:1px}
.mouse{left:591px;top:300px;width:19px;height:31px;border:2px solid var(--white);border-radius:10px}
.mouse::after{content:"";position:absolute;left:7px;top:5px;width:2px;height:7px;background:var(--white);border-radius:1px}

/* contact info */
.info-title{left:150px;top:590px;font-size:45px;font-style:italic;font-weight:800;letter-spacing:-.5px}
.info-row{left:148px;width:440px;display:flex;align-items:center;gap:30px}
.info-icon{width:72px;height:66px;background:var(--green);border-radius:8px;transform:skewX(-6deg);display:flex;align-items:center;justify-content:center;flex:none}
.info-icon svg{transform:skewX(6deg)}
.info-label{color:var(--green);font-size:24px;font-weight:700;line-height:1.15}
.info-value{font-size:24px;font-weight:700;line-height:1.25;white-space:nowrap}

/* form */
.form-card{left:613px;top:508px;width:411px;height:516px;background:var(--white);box-shadow:0 8px 30px rgba(0,0,0,.09);padding:48px 38px 0 38px}
.form-title{font-size:34px;font-style:italic;font-weight:800;margin-left:4px;margin-bottom:18px;letter-spacing:-.3px}
.field{width:338px;height:41px;background:var(--field);margin-bottom:7px;font-size:12px;color:#444;padding:11px 21px}
.field.message{height:112px;margin-bottom:9px}
.submit{width:322px;height:41px;margin-left:8px;background:var(--green);transform:skewX(-12deg);border-radius:6px;display:flex;align-items:center;justify-content:center;font-size:17px;font-weight:700;letter-spacing:.5px}
.submit span{transform:skewX(12deg)}

/* map */
.map{left:89px;top:1115px;width:1022px;height:522px;background:linear-gradient(135deg,#ececec,#d9d9d9 55%,#e6e6e6)}

/* newsletter & footer */
.footer-bg{left:0;top:1790px;width:1200px;height:534px}
.news{left:92px;top:1720px;width:1014px;height:151px}
.news-title{left:168px;top:1755px;font-size:46px;font-style:italic;font-weight:900;letter-spacing:.5px}
.news-sub{left:164px;top:1808px;font-size:19px}
.news-input{left:541px;top:1768px;width:360px;height:55px;background:var(--white);transform:skewX(-10deg);border-radius:8px 0 0 8px}
.news-input-text{left:565px;top:1783px;font-size:17px;color:#555}
.news-btn{left:874px;top:1768px;width:186px;height:55px;background:var(--ink);transform:skewX(-10deg);border-radius:8px;display:flex;align-items:center;justify-content:center}
.news-btn span{transform:skewX(10deg);color:var(--white);font-weight:700;font-size:17px;letter-spacing:.5px}

.foot-brand{left:87px;top:2070px;color:var(--white);font-size:38px;font-weight:800;letter-spacing:2px}
.foot-col h4{color:var(--white);font-size:17px;font-style:italic;font-weight:800;margin-bottom:8px}
.foot-col ul{list-style:none}
.foot-col li{color:var(--muted);font-size:13px;line-height:21.4px;display:flex;align-items:center;gap:6px;white-space:nowrap}
.foot-col li svg{flex:none}
.links{left:377px;top:2006px}
.contact{left:607px;top:2006px}
.world{left:562px;top:2050px;width:270px;height:160px;background:radial-gradient(ellipse at center,rgba(255,255,255,.12),rgba(255,255,255,0) 70%)}
.social{left:857px;top:2059px;display:flex;gap:9px}
.social span{width:37px;height:37px;border-radius:50%;background:var(--social);border:1px solid #333;display:flex;align-items:center;justify-content:center}
.rule{left:89px;top:2266px;width:1022px;height:1px;background:#2a2a2a}
.copy{left:0;top:2284px;width:1200px;text-align:center;color:var(--white);font-size:16px}
.to-top{left:1128px;top:2248px;width:40px;height:40px;border-radius:50%;background:var(--green);display:flex;align-items:center;justify-content:center}
</style>
</head>
<body>

<svg class="abs hero-bg" viewBox="0 0 1200 430" aria-hidden="true">
  <defs>
    <linearGradient id="heroPhoto" x1="0" y1="0" x2="1" y2="1">
      <stop offset="0" stop-color="#4a4c49"/>
      <stop offset=".5" stop-color="#3a3c3a"/>
      <stop offset="1" stop-color="#5b5e5a"/>
    </linearGradient>
  </defs>
  <path d="M0 0H1200V300C1195 390 1150 426 1080 426L640 382L0 316Z" fill="url(#heroPhoto)" role="img" aria-label="Close-up photograph of metal shavings"/>
  <path d="M0 316L645 383L0 405Z" fill="#59ff00"/>
</svg>

<nav class="abs nav">
  <div class="brand">TARN LOCK</div>
  <ul class="nav-links">
    <li>WHY VELKRIN MANUFACTURING?</li>
    <li>WHAT WE DO</li>
    <li>HOW WE MAKE IT BETTER</li>
    <li>CAPABILITIES</li>
    <li>GALLERY</li>
    <li>ABOUT US</li>
    <li>WISDOM</li>
  </ul>
  <div class="nav-cta">CONTACT</div>
</nav>

<h1 class="abs hero-title">CONTACT</h1>
<div class="abs mouse"></div>

<h2 class="abs info-title">CONTACT INFO</h2>

<div class="abs info-row" style="top:668px">
  <div class="info-icon"><svg width="28" height="28" viewBox="0 0 24 24"><path d="M6.6 10.8a15 15 0 0 0 6.6 6.6l2.2-2.2c.3-.3.7-.4 1-.2 1.1.4 2.3.6 3.6.6.6 0 1 .4 1 1V20c0 .6-.4 1-1 1A17 17 0 0 1 3 4c0-.6.4-1 1-1h3.5c.6 0 1 .4 1 1 0 1.2.2 2.4.6 3.6.1.3 0 .7-.2 1z" fill="#111"/></svg></div>
  <div><div class="info-label">Phone :</div><div class="info-value">612 555 0148</div></div>
</div>
<div class="abs info-row" style="top:761px">
  <div class="info-icon"><svg width="28" height="24" viewBox="0 0 24 20"><path d="M2 2h20v2l-10 7L2 4z M2 6.5l10 7 10-7V18H2z" fill="#111"/></svg></div>
  <div><div class="info-label">Email:</div><div class="info-value">info@tarnlock-mfg.com</div></div>
</div>
<div class="abs info-row" style="top:855px">
  <div class="info-icon"><svg width="26" height="32" viewBox="0 0 24 30"><path d="M12 0a11 11 0 0 0-11 11c0 8 11 19 11 19s11-11 11-19A11 11 0 0 0 12 0zm0 15a4 4 0 1 1 0-8 4 4 0 0 1 0 8z" fill="#111"/></svg></div>
  <div><div class="info-label">Address :</div><div class="info-value">Some goes address here</div></div>
</div>

<form class="abs form-card">
  <h2 class="form-title">GET IN TOUCH</h2>
  <div class="field">Name</div>
  <div class="field">Company Name</div>
  <div class="field">Phone Number</div>
  <div class="field">Email</div>
  <div class="field message">Message</div>
  <div class="submit"><span>SUBMIT</span></div>
</form>

<div class="abs map" role="img" aria-label="Street map showing the company location"></div>

<svg class="abs footer-bg" viewBox="0 0 1200 534" aria-hidden="true">
  <path d="M0 118L1080 8Q1190 0 1200 120V534H0Z" fill="#000"/>
</svg>

<svg class="abs news" viewBox="0 0 1014 151" aria-hidden="true">
  <path d="M38 0H1002Q1016 0 1012 14L982 135Q978 151 962 151H14Q-2 151 2 135L24 14Q28 0 38 0Z" fill="#59ff00"/>
</svg>
<div class="abs news-title">NEWSLETTER</div>
<div class="abs news-sub">Subscribe to our newsletter</div>
<div class="abs news-input"></div>
<div class="abs news-input-text">Enter your email</div>
<div class="abs news-btn"><span>SUBSCRIBE</span></div>

<div class="abs foot-brand">TARN LOCK</div>
<div class="abs world" role="img" aria-label="Faint dotted world map decoration"></div>

<div class="abs foot-col links">
  <h4>USEFUL LINKS</h4>
  <ul>
    <li>Why Velkrin Manufacturing?</li>
    <li>What we do</li>
    <li>How we make it better</li>
    <li>Capabilities</li>
    <li>About us</li>
    <li>Gallery</li>
    <li>Wisdom</li>
  </ul>
</div>
<div class="abs foot-col contact">
  <h4>CONTACT US</h4>
  <ul>
    <li><svg width="10" height="12" viewBox="0 0 24 30"><path d="M12 0a11 11 0 0 0-11 11c0 8 11 19 11 19s11-11 11-19A11 11 0 0 0 12 0zm0 15a4 4 0 1 1 0-8 4 4 0 0 1 0 8z" fill="#59ff00"/></svg>Some goes address here</li>
    <li><svg width="11" height="10" viewBox="0 0 24 20"><path d="M2 2h20v2l-10 7L2 4z M2 6.5l10 7 10-7V18H2z" fill="#59ff00"/></svg>hello@velkrin-mfg.com</li>
    <li><svg width="11" height="11" viewBox="0 0 24 24"><path d="M6.6 10.8a15 15 0 0 0 6.6 6.6l2.2-2.2c.3-.3.7-.4 1-.2 1.1.4 2.3.6 3.6.6.6 0 1 .4 1 1V20c0 .6-.4 1-1 1A17 17 0 0 1 3 4c0-.6.4-1 1-1h3.5c.6 0 1 .4 1 1 0 1.2.2 2.4.6 3.6.1.3 0 .7-.2 1z" fill="#59ff00"/></svg>+1 612 555 0147</li>
    <li><svg width="11" height="11" viewBox="0 0 24 24"><path d="M6 2h12v5H6z M3 8h18v9h-3v5H6v-5H3z M8 14v6h8v-6z" fill="#59ff00"/></svg>+1 612 555 0193</li>
  </ul>
</div>

<div class="abs social" aria-label="Social links">
  <span><svg width="14" height="14" viewBox="0 0 24 24"><circle cx="12" cy="12" r="9" stroke="#fff" stroke-width="2" fill="none"/><path d="M3 12h18M12 3c3 3 3 15 0 18M12 3c-3 3-3 15 0 18" stroke="#fff" stroke-width="1.6" fill="none"/></svg></span>
  <span><svg width="14" height="14" viewBox="0 0 24 24"><path d="M4 4h16v12H9l-5 4z" fill="#fff"/></svg></span>
  <span><svg width="14" height="14" viewBox="0 0 24 24"><circle cx="6" cy="12" r="3" fill="#fff"/><circle cx="18" cy="5" r="3" fill="#fff"/><circle cx="18" cy="19" r="3" fill="#fff"/><path d="M6 12L18 5M6 12l12 7" stroke="#fff" stroke-width="2"/></svg></span>
  <span><svg width="14" height="14" viewBox="0 0 24 24"><path d="M2 5h20v14H2z" fill="#fff"/><path d="M2 5l10 8 10-8" stroke="#1f1f1f" stroke-width="2" fill="none"/></svg></span>
</div>

<div class="abs rule"></div>
<div class="abs copy">©Copyright 2022 | All Rights Reserved</div>
<div class="abs to-top"><svg width="12" height="8" viewBox="0 0 12 8"><path d="M1 7L6 2L11 7" stroke="#111" stroke-width="1.6" fill="none"/></svg></div>

</body>
</html>
```